LDI Illustration Web Design

Create illustration web design company for Lumaviro Darsa Informatika (LDI). I more prefer design with illustration concept. Detail for requirement please see attach file. I'm also attach LDI logo. This logo had 2 type, 2D design and 3D design. You can chose one of them, or used both.
For the winner or had good design would be possible to private project to completeness this website
Attach file requirement is guidance for design, but any changes are welcome
Updates
Sorry, I forgot about contact. Please add menu contact. You can put this menu besides login menu or part of menu level #1, or put on some where to adjust your design. Menu contact will give pop up window to email LDI Company and Company Information (Address, Telephone, etc)
Target Market(s)
Company (Business To Business)
Industry/Entity Type
It Company
Look and feel
Each slider illustrates characteristics of the customer's brand and the style your logo design should communicate.

```html
<!DOCTYPE html>
<html lang="en">
<head>
<meta charset="utf-8">
<title>Lumaviro Darsa Informatika – Product</title>
<link rel="stylesheet" href="https://fonts.googleapis.com/css2?family=Arimo:wght@400;700&family=Open+Sans:wght@400;700&display=swap">
<style>
  :root {
    --navy-deep: #0a1b45;
    --navy: #0f1a3d;
    --navy-band: #0c2446;
    --footer: #0f1f42;
    --sky-top: #0a2257;
    --sky-mid: #1c4d8f;
    --sky-low: #8fb0d4;
    --snow: #eef3f7;
    --lime: #a8c81e;
    --lime-dark: #4f6a08;
    --nav-text: #c9d6ea;
    --body-text: #1b1f29;
    --footer-text: #4b5b7c;
    --white: #ffffff;
  }
  * { box-sizing: border-box; margin: 0; padding: 0; }
  html, body { width: 1200px; height: 1000px; overflow: hidden; }
  body { font-family: "Arimo", Arial, sans-serif; background: var(--navy-deep); }
  .page { position: relative; width: 1200px; height: 1000px; overflow: hidden; }

  .backdrop {
    position: absolute; inset: 0;
    background: linear-gradient(180deg, var(--sky-top) 0%, var(--sky-mid) 28%, var(--sky-low) 52%, #d9e5f0 64%, var(--snow) 72%, #f5f7f9 79%);
  }

  /* header */
  .brand { position: absolute; left: 22px; top: 18px; display: flex; align-items: center; gap: 10px; }
  .brand-dot { width: 40px; height: 40px; border-radius: 50%; background: var(--lime); }
  .brand-name { font-weight: 700; font-size: 44px; color: var(--lime); letter-spacing: 1px; line-height: 1; }

  .main-nav { position: absolute; left: 0; top: 0; width: 1200px; height: 70px; }
  .nav-link { position: absolute; top: 39px; color: var(--nav-text); text-decoration: none; font-size: 11px; font-weight: 700; letter-spacing: 0.3px; line-height: 13px; white-space: nowrap; }
  .nav-sep { position: absolute; top: 36px; width: 1px; height: 20px; background: #9aaccc; opacity: .7; }
  .nav-link.is-active::after { content: ""; position: absolute; left: -1px; right: -3px; top: 16px; height: 3px; background: #2a7fb8; }
  .login-btn {
    position: absolute; left: 1102px; top: 30px; width: 78px; height: 31px;
    background: linear-gradient(180deg, #2a8fd8, #0e5aa0); border: 1px solid #3aa2e8;
    color: #e8f4ff; font-size: 12px; font-weight: 700; display: flex; align-items: center; justify-content: center; text-decoration: none;
  }

  /* sidebar */
  .sidebar {
    position: absolute; left: 151px; top: 127px; width: 203px; height: 661px;
    background: repeating-linear-gradient(135deg, #101c42 0 2px, #0c1739 2px 4px);
    color: var(--white);
  }
  .side-group { position: absolute; left: 21px; }
  .side-title { font-size: 14px; font-weight: 700; letter-spacing: .4px; }
  .side-link { display: block; color: var(--white); text-decoration: none; font-size: 13px; }
  .side-rule { position: absolute; left: 20px; width: 158px; height: 1px; background: #4a5a86; }
  .side-link.is-current { border-bottom: 4px solid var(--lime-dark); display: inline-block; padding-bottom: 1px; }

  /* content */
  .content-hero {
    position: absolute; left: 354px; top: 127px; width: 693px; height: 369px;
    background:
      radial-gradient(ellipse 260px 170px at 56% 38%, rgba(255,255,255,.85), rgba(255,255,255,0) 75%),
      radial-gradient(ellipse 200px 120px at 30% 70%, rgba(255,255,255,.6), rgba(255,255,255,0) 75%),
      linear-gradient(180deg, #a9bfd9 0%, #c8d8e8 55%, #e6eef6 100%);
  }
  .content-text { position: absolute; left: 411px; top: 194px; width: 555px; color: var(--body-text); }
  .content-text h1 { font-size: 19px; font-weight: 700; margin-bottom: 20px; line-height: 22px; }
  .content-text p { font-size: 13px; line-height: 16px; }
  .content-text .gap { margin-top: 14px; }

  /* media band */
  .media-band { position: absolute; left: 354px; top: 496px; width: 693px; height: 211px; background: var(--navy-band); }
  .slide-arrow { position: absolute; top: 66px; width: 14px; height: 34px; }
  .feature-video {
    position: absolute; left: 49px; top: 14px; width: 201px; height: 184px;
    background: radial-gradient(circle at 40% 35%, #5fc7f0, #1b6dc0 55%, #0f3f86);
  }
  .play-icon { position: absolute; left: 65px; top: 53px; }
  .about-block { position: absolute; left: 262px; top: 12px; width: 96px; color: var(--white); }
  .about-block h2 { font-family: "Open Sans", Arial, sans-serif; font-size: 16px; font-weight: 700; line-height: 18px; margin-bottom: 9px; }
  .about-block p { font-family: "Open Sans", Arial, sans-serif; font-size: 4.6px; line-height: 6px; margin-bottom: 5px; color: #dfe7f2; }
  .thumb-panel { position: absolute; top: 0; width: 136px; height: 211px; background: #0a1f3f; }
  .thumb { position: absolute; width: 82px; height: 64px; background: radial-gradient(circle at 45% 40%, #5fd0f2, #1d78c4 60%, #114a8e); }
  .thumb-play { position: absolute; left: 29px; top: 20px; }
  .thumb-label { position: absolute; color: var(--white); font-family: "Open Sans", Arial, sans-serif; font-size: 7.5px; font-weight: 700; width: 82px; }
  .thumb-label span { display: block; font-weight: 400; font-size: 3.6px; line-height: 4.4px; color: #c7d4e6; margin-top: 2px; }

  /* lime band + pager */
  .lime-band {
    position: absolute; left: 0; top: 788px; width: 1200px; height: 34px;
    background: linear-gradient(180deg, #d7ea5a 0%, var(--lime) 35%, #7a9a10 75%, #3f5506 100%);
  }
  .pager { position: absolute; top: 797px; left: 468px; display: flex; gap: 27px; }
  .pager i { display: block; width: 15px; height: 15px; border-radius: 50%; background: radial-gradient(circle at 45% 40%, #9aa1a6, #5b6166); border: 1px solid #c9d0a0; }
  .pager i.is-active { background: radial-gradient(circle, #ffffff 0 3px, #8a9196 4px); }

  /* footer */
  .footer { position: absolute; left: 0; top: 822px; width: 1200px; height: 178px; background: var(--footer); }
  .footer-rule { position: absolute; left: 353px; top: 0; width: 1px; height: 66px; background: #2a3a60; }
  .footer-col { position: absolute; top: 34px; width: 218px; }
  .footer-col p { font-size: 9.6px; line-height: 11.7px; color: var(--footer-text); text-align: justify; letter-spacing: -0.05px; }
  .learn-btn {
    position: absolute; top: 135px; width: 78px; height: 18px; background: linear-gradient(180deg, #2aa2f0, #0c72c6);
    color: var(--white); font-size: 8px; display: flex; align-items: center; justify-content: center; text-decoration: none;
  }
  .newsletter { position: absolute; left: 896px; top: 150px; display: flex; }
  .newsletter-field { width: 208px; height: 17px; background: #4a4d52; color: #c7cad0; font-size: 8px; display: flex; align-items: center; gap: 5px; padding-left: 7px; }
  .subscribe-btn { margin-left: 11px; width: 66px; height: 17px; background: linear-gradient(180deg, #2aa2f0, #0c72c6); color: var(--white); font-size: 8px; display: flex; align-items: center; justify-content: center; }
</style>
</head>
<body>
<div class="page">
  <div class="backdrop" role="img" aria-label="Illustrated winter landscape: deep blue sky fading into clouds and snowy mountains"></div>

  <header>
    <div class="brand"><span class="brand-dot"></span><span class="brand-name">LDI</span></div>
    <nav class="main-nav">
      <a href="#" class="nav-link" style="left:489px">HOME</a>
      <span class="nav-sep" style="left:547px"></span>
      <a href="#" class="nav-link" style="left:569px">SERVICES</a>
      <span class="nav-sep" style="left:642px"></span>
      <a href="#" class="nav-link is-active" style="left:662px">PRODUCT</a>
      <span class="nav-sep" style="left:737px"></span>
      <a href="#" class="nav-link" style="left:759px">CLIENTS</a>
      <span class="nav-sep" style="left:833px"></span>
      <a href="#" class="nav-link" style="left:847px">COMPANY</a>
      <span class="nav-sep" style="left:929px"></span>
      <a href="#" class="nav-link" style="left:953px">BLOG</a>
      <span class="nav-sep" style="left:1006px"></span>
      <a href="#" class="nav-link" style="left:1025px">CONTACT</a>
    </nav>
    <a href="#" class="login-btn">LOGIN</a>
  </header>

  <aside class="sidebar">
    <div class="side-group" style="top:44px"><div class="side-title">SERVICES</div></div>
    <div class="side-group" style="top:83px">
      <a href="#" class="side-link">Software Development</a>
      <a href="#" class="side-link" style="margin-top:15px">GIS Software</a>
      <a href="#" class="side-link" style="margin-top:15px">Mobile Development</a>
      <a href="#" class="side-link" style="margin-top:15px">Radio Frequency &amp; Planning</a>
    </div>
    <div class="side-rule" style="top:221px"></div>
    <div class="side-group" style="top:257px"><div class="side-title">PRODUCT</div></div>
    <div class="side-group" style="top:287px"><a href="#" class="side-link is-current">Workbook</a></div>
    <div class="side-rule" style="top:337px"></div>
    <div class="side-group" style="top:368px"><div class="side-title">CLIENTS</div></div>
    <div class="side-rule" style="top:413px"></div>
    <div class="side-group" style="top:447px"><div class="side-title">COMPANY</div></div>
    <div class="side-group" style="top:476px">
      <a href="#" class="side-link">About LDI</a>
      <a href="#" class="side-link" style="margin-top:14px">Contact Us</a>
    </div>
  </aside>

  <section>
    <div class="content-hero" role="img" aria-label="Illustration of soft clouds with glowing light particles"></div>
    <div class="content-text">
      <h1>Product</h1>
      <p>Lorem ipsum dolor sit amet, consectetur adipisicing elit, sed do eiusmod tempor incididunt ut labore et dolore magna aliqua. Ut enim ad minim veniam, quis nostrud exercitation ullamco laboris nisi ut aliquip ex ea commodo consequat.</p>
      <p>Lorem ipsum dolor sit amet, consectetur adipisicing elit, sed do eiusmod tempor incididunt ut labore et dolore magna aliqua. Ut enim ad minim veniam, quis nostrud exercitation ullamco laboris nisi ut aliquip ex ea commodo consequat.</p>
      <p class="gap">Lorem ipsum dolor sit amet, consectetur adipisicing elit, sed do eiusmod tempor incididunt ut labore et dolore magna aliqua. Ut enim ad minim veniam, quis nostrud exercitation ullamco laboris nisi ut aliquip ex ea commodo consequat.</p>
      <p>Lorem ipsum dolor sit amet, consectetur adipisicing elit, sed do eiusmod tempor incididunt ut labore et dolore magna aliqua. Ut enim ad minim veniam, quis nostrud exercitation ullamco laboris nisi ut aliquip ex ea commodo consequat.</p>
    </div>
  </section>

  <section class="media-band">
    <svg class="slide-arrow" style="left:18px" viewBox="0 0 14 34"><path d="M11 2 L3 17 L11 32" fill="none" stroke="#fff" stroke-width="3"/></svg>
    <svg class="slide-arrow" style="left:367px" viewBox="0 0 14 34"><path d="M3 2 L11 17 L3 32" fill="none" stroke="#fff" stroke-width="3"/></svg>

    <div class="feature-video" role="img" aria-label="Video still of blue glowing light particles">
      <svg class="play-icon" width="72" height="72" viewBox="0 0 72 72"><circle cx="36" cy="36" r="35" fill="#0b2c55"/><path d="M27 20 L53 36 L27 52 Z" fill="#2aa0e0"/></svg>
    </div>

    <div class="about-block">
      <h2>about us</h2>
      <p>Lorem ipsum dolor sit amet, consectetur adipisicing elit, sed do eiusmod tempor incididunt ut labore et dolore magna aliqua ut enim.</p>
      <p>Lorem ipsum dolor sit amet, consectetur adipisicing elit, sed do eiusmod tempor incididunt ut labore et dolore magna aliqua ut enim.</p>
      <p>Lorem ipsum dolor sit amet, consectetur adipisicing elit, sed do eiusmod tempor incididunt ut labore et dolore magna aliqua ut enim.</p>
      <p>Lorem ipsum dolor sit amet, consectetur adipisicing elit, sed do eiusmod tempor incididunt ut labore et dolore magna aliqua ut enim.</p>
    </div>

    <div class="thumb-panel" style="left:400px"></div>
    <div class="thumb-panel" style="left:548px"></div>

    <div class="thumb" style="left:419px;top:8px" role="img" aria-label="Video thumbnail with blue light particles"><svg class="thumb-play" width="24" height="24" viewBox="0 0 24 24"><circle cx="12" cy="12" r="11" fill="#0b2c55"/><path d="M9 6 L18 12 L9 18 Z" fill="#2aa0e0"/></svg></div>
    <div class="thumb" style="left:568px;top:8px" role="img" aria-label="Video thumbnail with blue light particles"><svg class="thumb-play" width="24" height="24" viewBox="0 0 24 24"><circle cx="12" cy="12" r="11" fill="#0b2c55"/><path d="M9 6 L18 12 L9 18 Z" fill="#2aa0e0"/></svg></div>
    <div class="thumb" style="left:419px;top:107px" role="img" aria-label="Video thumbnail with blue light particles"><svg class="thumb-play" width="24" height="24" viewBox="0 0 24 24"><circle cx="12" cy="12" r="11" fill="#0b2c55"/><path d="M9 6 L18 12 L9 18 Z" fill="#2aa0e0"/></svg></div>
    <div class="thumb" style="left:568px;top:107px" role="img" aria-label="Video thumbnail with blue light particles"><svg class="thumb-play" width="24" height="24" viewBox="0 0 24 24"><circle cx="12" cy="12" r="11" fill="#0b2c55"/><path d="M9 6 L18 12 L9 18 Z" fill="#2aa0e0"/></svg></div>

    <div class="thumb-label" style="left:419px;top:76px">sample text<span>Lorem ipsum dolor sit amet elit sed do</span></div>
    <div class="thumb-label" style="left:568px;top:76px">sample text<span>Lorem ipsum dolor sit amet elit sed do</span></div>
    <div class="thumb-label" style="left:419px;top:175px">sample text<span>Lorem ipsum dolor sit amet elit sed do</span></div>
    <div class="thumb-label" style="left:568px;top:175px">sample text<span>Lorem ipsum dolor sit amet elit sed do</span></div>
  </section>

  <div class="lime-band"></div>
  <div class="pager"><i class="is-active"></i><i></i><i></i><i></i><i></i><i></i><i></i></div>

  <footer class="footer">
    <div class="footer-rule"></div>
    <div class="footer-col" style="left:406px"><p>Lorem ipsum badama dolor sit amet, consectetur adipisicing elit, sed do eiusmod tempor incididunt ut labore et dolore magna aliqua. Ut enim ad minim veniam, quis nostrud exercitation ullamco laboris nisi ut aliquip ex ea commodo consequat. Duis aute irure dolor in reprehenderit in voluptate velit esse cillum dolore eu.</p></div>
    <div class="footer-col" style="left:632px"><p>Lorem ipsum badama dolor sit amet, consectetur adipisicing elit, sed do eiusmod tempor incididunt ut labore et dolore magna aliqua. Ut enim ad minim veniam, quis nostrud exercitation ullamco laboris nisi ut aliquip ex ea commodo consequat. Duis aute irure dolor in reprehenderit in voluptate velit esse cillum dolore eu.</p></div>
    <a href="#" class="learn-btn" style="left:406px">LEARN MORE</a>
    <a href="#" class="learn-btn" style="left:632px">LEARN MORE</a>
    <div class="newsletter">
      <div class="newsletter-field">
        <svg width="11" height="8" viewBox="0 0 11 8"><rect x=".5" y=".5" width="10" height="7" fill="none" stroke="#e0e0e0"/><path d="M.5 .5 L5.5 4.5 L10.5 .5" fill="none" stroke="#e0e0e0"/></svg>
        your email address...
      </div>
      <div class="subscribe-btn">SUBSCRIBE</div>
    </div>
  </footer>
</div>
</body>
</html>
```